Website for Brisk Morning Rambles who develops hiking guides for easy to moderate hikes of up to 4 hours

Website for a company who creates hiking guides for State Parks and other tourist destinations. Looking for the ability to showcase various hiking destinations, our hiking guides, product favorites and blog with the ability to sell our hiking guides via the website shopping cart. Should feature photos from our hiking guides with the the ability to include photo thumbnails that can be expanded.

We need the ability to self manage the website - including ability to self update, add pages, graphics, etc.

While we want to have high quality photos we still want the pages to load quickly

Target Market(s)

People who enjoy nature and like to walk or hike for up to half a day on trails in a specific destination.
Adventure travelers who loves nature and the outdoors

Industry/Entity Type

Travel

Font styles to use
Sans Serif

Colors

Designer to choose colors to be used in the design.

Requirements
Must have
• We are looking for a fully operational WIX design for www.briskmorningrambles.example that has the following:
• 1. Menus - We want the ability to have multiple drop-down menus.
• 2. E-commerce – the ability to accept orders for books that we publish.
• 3. A form that can be filled out online to provide feedback on our hiking guides. (We will give the fields that need to be filled out.)
• 4. Pictures - Incorporates Professional Pictures– thumbnails that can be clicked to be larger, and pictures included with copy.
• 5. Logo – Our logo can be provided.
• 6. Domain Name - We already have the domain name briskmorningrambles.example
• 7. We want to be able to take your design and do our own changes via WIX.
• 8. The home page should have the ability to have scrolling photos – up to 10 images that can be easily updated.
• 9. Password protected pages that can only be accessed by a password.
• 10. We have a color palate that should be used for the site design
• 11. Six (6) major tabs
• #1 Home Page – Scrolling photos, general overview, hiking guide summary, other
• # 2 Destinations – Summary of all guides published, with sub-pages on each guide
• #3 Favorite products
• # 4 Blog – Blog index and all blogs
• #5 Photography
• #6 Contact us – form for feedback, links to other sites etc.
• We also need the ability to link to our Folkbook and Snapgrid Accounts.
• Photos included as an example for our Home page.
• Please use the colors in our color palette provided as an attachment
Nice to have
• Examples of website designs we like as a reference
• https://www.roamingtheparkers.example
• https://www.torvalegrove.example/index.php
Should not have
• Colors that do not align with our color palette that is included as an attachment.

```html
<!DOCTYPE html>
<html lang="en">
<head>
<meta charset="utf-8">
<title>Brisk Morning Rambles</title>
<link href="https://fonts.googleapis.com/css2?family=Montserrat:ital,wght@0,400;0,500;0,600;0,700;0,800;1,400;1,500&display=swap" rel="stylesheet">
<style>
:root{
  --blue:#2d5597;
  --orange:#d45a30;
  --ink:#333333;
  --muted:#5a5a5a;
  --pale:#eef2fa;
  --footer:#2a2a2a;
  --white:#ffffff;
}
*{margin:0;padding:0;box-sizing:border-box}
html,body{width:1200px;height:4054px;overflow:hidden;background:var(--white)}
body{position:relative;font-family:'Montserrat',sans-serif;color:var(--ink)}
.abs{position:absolute}

/* header */
.brand{left:172px;top:40px;display:flex;align-items:center;gap:10px}
.brand-mark{width:26px;height:26px;background:var(--orange)}
.brand-name{font-size:19px;font-weight:700;color:var(--blue);line-height:1.1;width:130px}
.util{top:30px;display:flex;align-items:center;gap:8px;font-size:12px;font-weight:600;color:var(--ink)}
.util .dot{width:24px;height:24px;border-radius:50%;display:flex;align-items:center;justify-content:center}
.nav{font-size:12.5px;font-weight:600;letter-spacing:.3px;color:#444}
.nav span{position:absolute;white-space:nowrap}

/* hero */
.hero{left:75px;top:129px;width:1050px;height:528px;background:linear-gradient(180deg,#2f5bb5 0%,#4c7fd0 45%,#b88a55 68%,#7a5a35 100%)}
.hero-copy{left:660px;top:262px;width:390px;display:flex;flex-direction:column;align-items:flex-start}
.hero-title{font-size:40px;font-weight:800;line-height:44px;color:var(--white)}
.btn{background:var(--orange);color:var(--white);border-radius:20px;font-weight:700;font-size:12px;display:flex;align-items:center;justify-content:center;letter-spacing:.3px}
.hero-btn{margin-top:14px;width:117px;height:33px}

/* section headings */
.h-sec{font-size:24px;font-weight:700;color:var(--blue);line-height:28px;letter-spacing:.2px}
.center{left:0;width:1200px;text-align:center}
.body-copy{font-size:11px;line-height:21px;color:var(--muted)}

/* product */
.product{left:172px;top:1041px;width:856px;height:361px;border:3px solid var(--blue)}
.product-photo{left:3px;top:3px;width:378px;height:352px;background:linear-gradient(180deg,#7eb3e0 0%,#3d6f4a 40%,#2d4a30 70%,#6d6d6d 100%)}
.heart{left:316px;top:30px;width:26px;height:26px;border-radius:50%;background:var(--orange);display:flex;align-items:center;justify-content:center}
.product-info{left:384px;top:0;width:466px;text-align:center}
.product-title{margin-top:110px;font-size:18px;font-weight:600;color:var(--ink)}
.product-price{margin-top:18px;font-size:20px;font-weight:700;color:var(--blue)}
.product-desc{margin:8px auto 0;width:250px;font-size:10.5px;line-height:19px;color:var(--muted)}
.view-all{left:457px;top:1442px;display:flex;align-items:center;gap:14px;font-size:11.5px;font-weight:600;color:var(--ink)}
.view-all .rule{width:80px;height:2px;background:var(--ink)}

/* reviews */
.reviews{left:75px;top:1523px;width:1050px;height:537px;background:linear-gradient(180deg,#d3552e 0%,#db6a3f 60%,#d45a33 100%)}
.reviews-inner{left:0;top:72px;width:1050px;display:flex;flex-direction:column;align-items:center;text-align:center;color:var(--white)}
.quote{font-size:110px;font-weight:800;line-height:90px;height:90px}
.reviews-title{margin-top:8px;font-size:22px;font-weight:700}
.reviews-text{margin-top:22px;width:520px;font-style:italic;font-size:18px;line-height:28.5px}
.reviews-name{margin-top:18px;font-size:17px;font-weight:700}

/* guides */
.guide{width:300px}
.guide-photo{width:197px;height:206px}
.guide-title{margin-top:24px;display:flex;align-items:center;gap:10px;font-size:14px;font-weight:700;color:var(--ink)}
.guide-title .dash{width:18px;height:2px;background:var(--ink)}
.guide-copy{margin:12px 0 0 27px;width:225px;font-size:10.5px;line-height:20px;color:var(--muted)}

/* destinations */
.dest-band{left:75px;top:2707px;width:1050px;height:659px;background:var(--pale)}
.tile{width:201px;height:198px}
.tile-note{display:flex;align-items:center;justify-content:center;text-align:center;font-size:12px;font-weight:600;line-height:20px;color:var(--white);padding:0 30px}

/* blog */
.blog{top:3610px;height:265px;border:3px solid var(--blue);text-align:center}
.blog.featured{border-color:var(--orange)}
.blog-date{margin-top:62px;font-size:14px;font-weight:600;color:var(--ink)}
.blog-rule{margin:14px auto 0;width:52px;height:3px;background:#8a8a8a}
.blog-copy{margin:18px auto 0;width:215px;font-size:10.5px;line-height:20px;color:var(--muted)}

/* footer */
.footer{left:0;top:3963px;width:1200px;height:91px;background:var(--footer)}
.copyright{left:172px;top:40px;font-size:11.5px;color:#e6e6e6}
.social{left:826px;top:40px;display:flex;gap:14px;font-size:11px;font-weight:600;color:var(--white)}
</style>
</head>
<body>

<header>
  <div class="abs brand"><div class="brand-mark"></div><div class="brand-name">Brisk Morning Rambles</div></div>
  <div class="abs util" style="left:785px">
    <div class="dot" style="background:var(--blue)">
      <svg width="12" height="12" viewBox="0 0 12 12"><path d="M1 2h2l1.5 6h5l1.5-4.5H4" fill="none" stroke="#fff" stroke-width="1.4"/><circle cx="5" cy="10.2" r="1" fill="#fff"/><circle cx="9" cy="10.2" r="1" fill="#fff"/></svg>
    </div>SHOPPING CART
  </div>
  <div class="abs util" style="left:948px">
    <div class="dot" style="background:var(--orange)">
      <svg width="12" height="12" viewBox="0 0 12 12"><circle cx="6" cy="4" r="2.3" fill="#fff"/><path d="M1.8 11c.5-3 2-4.2 4.2-4.2s3.7 1.2 4.2 4.2z" fill="#fff"/></svg>
    </div>LOG IN
  </div>
  <nav class="abs nav" style="left:0;top:89px">
    <span style="left:337px">HOME</span>
    <span style="left:411px">DESTINATIONS ▾</span>
    <span style="left:545px">FAVORITE PRODUCTS ▾</span>
    <span style="left:726px">BLOG</span>
    <span style="left:797px">PHOTOGRAPHY</span>
    <span style="left:935px">CONTACT US</span>
  </nav>
</header>

<section class="abs hero" role="img" aria-label="Slideshow photo: mushroom-shaped sandstone rock in a desert valley under a deep blue sky"></section>
<svg class="abs" style="left:110px;top:368px" width="28" height="50" viewBox="0 0 28 50"><path d="M24 2L4 25l20 23" fill="none" stroke="#fff" stroke-width="2"/></svg>
<svg class="abs" style="left:1068px;top:368px" width="28" height="50" viewBox="0 0 28 50"><path d="M4 2l20 23L4 48" fill="none" stroke="#fff" stroke-width="2"/></svg>
<div class="abs hero-copy">
  <h1 class="hero-title">Welcome to<br>Brisk Morning<br>Rambles</h1>
  <div class="btn hero-btn">READ MORE</div>
</div>

<section>
  <h2 class="abs h-sec" style="left:172px;top:715px">ABOUT<br>BRISK MORNING RAMBLES</h2>
  <p class="abs body-copy" style="left:172px;top:790px;width:400px">Sed ut perspiciatis unde omnis iste natus error sit voluptatem accusantium doloremque laudantium, totam rem aperiam, eaque ipsa quae ab illo invent ore veritatis et quasi architecto beatae vitae dicta sunt explicabo. Nemo eim psam voluptatem quia voluptas sit aspernatur aut odit aut fugit, sed quilora consequuntur magni dolores eos qui ratione voluptate.</p>
  <p class="abs body-copy" style="left:630px;top:790px;width:400px">Sed ut perspiciatis unde omnis iste natus error sit voluptatem accusantium doloremque laudantium, totam rem aperiam, eaque ipsa quae ab illo invent ore veritatis et quasi architecto beatae vitae dicta sunt explicabo. Nemo eim psam voluptatem quia voluptas sit aspernatur aut odit aut fugit, sed quilora consequuntur magni dolores eos qui ratione voluptate.</p>
</section>

<section>
  <h2 class="abs h-sec" style="left:172px;top:980px">PRODUCT FAVORITES</h2>
  <div class="abs product">
    <div class="abs product-photo" role="img" aria-label="Product photo: rolled blue sleeping mat strapped to a green backpack on a rock above a forested lake">
      <div class="abs heart"><svg width="12" height="12" viewBox="0 0 12 12"><path d="M6 10.5L1.5 6A2.4 2.4 0 016 2.8 2.4 2.4 0 0110.5 6z" fill="none" stroke="#fff" stroke-width="1.3"/></svg></div>
    </div>
    <div class="abs product-info">
      <div class="product-title">Sednis isttusulore</div>
      <div class="product-price">$250.00</div>
      <p class="product-desc">Sed ut perspiciatis unde omnis iste natus erro sit voluptatem accusantium dolorem</p>
      <div class="btn" style="width:102px;height:33px;margin:22px auto 0;position:relative;left:4px">BUY NOW</div>
    </div>
  </div>
  <div class="abs view-all"><div class="rule"></div>View All Products
    <svg width="10" height="12" viewBox="0 0 10 12" style="margin-left:6px"><path d="M2 1l5 5-5 5" fill="none" stroke="#333" stroke-width="2"/></svg>
  </div>
</section>

<section class="abs reviews" role="img" aria-label="Reviews band: hiker resting on red desert rock, tinted orange">
  <div class="abs reviews-inner">
    <div class="quote">“</div>
    <h2 class="reviews-title">BEST REVIEWS</h2>
    <p class="reviews-text">Sed ut perspiciatis unde omnis iste natus sit voluptatem accusantium doloremque laudantium, totam rem aperiam, eaque ipsa quae ab illo invent ore veritatis et quasi architecto beatae vitae dicta sunt explicabo.mpsam voluptatem</p>
    <div class="reviews-name">- Wren Halloway</div>
  </div>
  <svg class="abs" style="left:52px;top:245px" width="28" height="50" viewBox="0 0 28 50"><path d="M24 2L4 25l20 23" fill="none" stroke="#fff" stroke-width="2"/></svg>
  <svg class="abs" style="left:983px;top:245px" width="28" height="50" viewBox="0 0 28 50"><path d="M4 2l20 23L4 48" fill="none" stroke="#fff" stroke-width="2"/></svg>
</section>

<section>
  <h2 class="abs h-sec center" style="top:2163px">OUR HIKING GUIDES</h2>
  <div class="abs guide" style="left:172px;top:2241px">
    <div class="guide-photo" role="img" aria-label="Photo: open city travel guidebook on a wooden table" style="background:linear-gradient(135deg,#8a6a4a,#d9c9b0 50%,#6b4a30)"></div>
    <div class="guide-title"><span class="dash"></span>Neue sedorro uisuam</div>
    <p class="guide-copy">Sed ut perspiciatis unde omnis iste ntus error sit voluptatem accusantium dolem que laudantium, totam rem aperiam, eue ipsa quae ab illo inventore verit.</p>
  </div>
  <div class="abs guide" style="left:482px;top:2241px">
    <div class="guide-photo" role="img" aria-label="Photo: leather travel journal with a pine sprig on dark wood" style="background:linear-gradient(135deg,#2a1d12,#7a5433 50%,#3a2a1a)"></div>
    <div class="guide-title"><span class="dash"></span>Neue sedorro uisuam</div>
    <p class="guide-copy">Sed ut perspiciatis unde omnis iste ntus error sit voluptatem accusantium dolem que laudantium, totam rem aperiam, eue ipsa quae ab illo inventore verit.</p>
  </div>
  <div class="abs guide" style="left:791px;top:2241px">
    <div class="guide-photo" role="img" aria-label="Photo: red hiking guide book on weathered wooden planks" style="background:linear-gradient(90deg,#4a3a2c 0%,#4a3a2c 20%,#d8332a 20%,#d8332a 80%,#4a3a2c 80%)"></div>
    <div class="guide-title"><span class="dash"></span>Neue sedorro uisuam</div>
    <p class="guide-copy">Sed ut perspiciatis unde omnis iste ntus error sit voluptatem accusantium dolem que laudantium, totam rem aperiam, eue ipsa quae ab illo inventore verit.</p>
  </div>
</section>

<section>
  <div class="abs dest-band"></div>
  <h2 class="abs h-sec center" style="top:2766px">HIKING DESTINATIONS</h2>
  <div class="abs tile" style="left:172px;top:2829px;background:linear-gradient(180deg,#3e6fb5,#6c7f90 50%,#3a4a35)" role="img" aria-label="Destination photo: misty mountain cliffs"></div>
  <div class="abs tile" style="left:389px;top:2829px;background:linear-gradient(180deg,#3f79d0,#a9c3e0 45%,#3a4a3a 75%,#2a4a6a)" role="img" aria-label="Destination photo: castle above a lake"></div>
  <div class="abs tile" style="left:608px;top:2829px;background:linear-gradient(180deg,#5a86c0,#3a5a4a 40%,#1e3f66)" role="img" aria-label="Destination photo: winding fjord between hills"></div>
  <div class="abs tile" style="left:827px;top:2829px;background:linear-gradient(180deg,#2f5bb5,#b98a55 60%,#7a5a35)" role="img" aria-label="Destination photo: mushroom rock in the desert"></div>
  <div class="abs tile" style="left:172px;top:3041px;background:linear-gradient(180deg,#3a6ac0,#8aa5c5 45%,#3a3a35)" role="img" aria-label="Destination photo: old stone granaries on a hill"></div>
  <div class="abs tile" style="left:389px;top:3041px;background:linear-gradient(180deg,#c9d3d8,#6f8a8e 50%,#2e4a48)" role="img" aria-label="Destination photo: train on a bridge over snowy forest"></div>
  <div class="abs tile tile-note" style="left:608px;top:3041px;background:linear-gradient(180deg,#d4592e,#b8462a)" role="img" aria-label="Destination photo: red desert dunes, tinted orange">Sed ut perspiciatis unde omnis iste ntus it voomnis ilontu</div>
  <div class="abs tile" style="left:827px;top:3041px;background:linear-gradient(180deg,#4a7ac0,#3e6a8a 40%,#4a6a3a)" role="img" aria-label="Destination photo: switchback mountain road"></div>
  <div class="abs tile" style="left:172px;top:3259px;background:linear-gradient(180deg,#6fa6d8,#4f8a3a 45%,#2e5a28)" role="img" aria-label="Destination photo: stone wall path over green hills"></div>
  <div class="abs tile" style="left:389px;top:3259px;background:linear-gradient(180deg,#3a6fc5,#9ab5d5 40%,#6a5a3a 70%,#4a4a2a)" role="img" aria-label="Destination photo: ruined tower above a valley"></div>
  <div class="abs tile" style="left:608px;top:3259px;background:linear-gradient(180deg,#4a86d0,#5a7a5a 45%,#2a5a4a)" role="img" aria-label="Destination photo: mountain lake with green slopes"></div>
  <div class="abs tile" style="left:827px;top:3259px;background:linear-gradient(180deg,#3a6fc5,#c98a50 50%,#8a4a2a)" role="img" aria-label="Destination photo: hilltop fort reflected in water"></div>
</section>

<section>
  <h2 class="abs h-sec center" style="top:3544px">LATEST BLOG</h2>
  <article class="abs blog" style="left:172px;width:286px">
    <div class="blog-date">July 22 2019</div><div class="blog-rule"></div>
    <p class="blog-copy">Sed ut perspiciatis unde omnis iste ntus error sit voluptatem accusantium dolem que laudantium, totam rem aperiam, eue ipsa quae ab illo inventore verit.</p>
  </article>
  <article class="abs blog featured" style="left:455px;width:289px">
    <div class="blog-date">July 22 2019</div><div class="blog-rule"></div>
    <p class="blog-copy">Sed ut perspiciatis unde omnis iste ntus error sit voluptatem accusantium dolem que laudantium, totam rem aperiam, eue ipsa quae ab illo inventore verit.</p>
  </article>
  <article class="abs blog" style="left:741px;width:285px">
    <div class="blog-date">July 22 2019</div><div class="blog-rule"></div>
    <p class="blog-copy">Sed ut perspiciatis unde omnis iste ntus error sit voluptatem accusantium dolem que laudantium, totam rem aperiam, eue ipsa quae ab illo inventore verit.</p>
  </article>
</section>

<footer class="abs footer">
  <div class="abs copyright">Copyright 2019 All Rights Reserved</div>
  <div class="abs social"><span>Folkbook</span><span>Snapgrid</span><span>Chirper</span><span>Linkwork</span><span>Viewtube</span></div>
</footer>

</body>
</html>
```